Design a modern, classy & professional business card for an online real estate agency, specializing in medium-luxury properties in Thailand and later in Singapore and UK.

Possible design ideas so far: (not essential)

- curved corner(s) to the card, white on front & turquoise on back or visa versa.

- front of card - clear and simple, company name in metallic grey/monochrome, logo graphic & company name on front in spot UV or embossed/debossed effect.

- back of card - large, close-cropped, 'ghost' patterns of the C-shaped curves of logo, or company name repeated on back of card in spot UV.

Target Market(s)

- young to middle-aged professionals mainly (but ideally should design should suit all)

- UK, US,EU,AUS & ASIAN mainly (but ideally should design should suit all countries)

Industry/Entity Type

Real Estate

Requirements
Must have
• THEME:
- Luxurious & Modern
- Clean & striking
- Unique & creative

INFO:
- Logo & company name on front
- Contact details on back:

Tobias Hennlund
Managing Director

www.velmontestates.asia
www.velmontestates.co.uk

Tel: 083-274-6159
email: tobias@velmontestates.asia

(contact details can be displayed in any order as suites design.)

Nice to have
• - curved corner(s) to the card, white on front & turquoise on back or visa versa.

Should not have
• - No generic images of properties, palm trees/coconut trees etc.

- No other other bold colors, except for main turquoise, grey, metallic white & black theme.

- No obvious business card templates

```html
<!DOCTYPE html>
<html lang="en">
<head>
<meta charset="utf-8">
<title>Velmont Estates – Business Card</title>
<link href="https://fonts.googleapis.com/css2?family=Tinos&family=Arimo&display=swap" rel="stylesheet">
<style>
  :root {
    --stage-light: #8a8a8a;
    --stage-dark: #2a2a2a;
    --card-grey: #bdbdbd;
    --card-white: #ffffff;
    --turquoise: #2ccdc8;
    --ghost-white: rgba(255, 255, 255, 0.55);
    --ghost-teal: rgba(160, 215, 212, 0.45);
    --metal-grey: #6f6f6f;
    --ink: #2a1a1a;
    --rule: #333333;
  }
  * { margin: 0; padding: 0; box-sizing: border-box; }
  html, body { width: 1200px; height: 889px; overflow: hidden; }
  body {
    position: relative;
    background: radial-gradient(ellipse at 45% 45%, var(--stage-light) 0%, #5e5e5e 45%, var(--stage-dark) 100%);
    font-family: "Arimo", Arial, sans-serif;
  }
  .card {
    position: absolute;
    width: 710px;
    height: 406px;
    border-radius: 50px;
    overflow: hidden;
    box-shadow: 0 14px 30px rgba(0, 0, 0, 0.35);
  }
  .card--back { left: 85px; top: 62px; background: var(--card-grey); }
  .card--front { left: 425px; top: 407px; background: var(--card-white); }
  .ghost-pattern { position: absolute; inset: 0; }
  .card--back .ghost-pattern {
    background:
      radial-gradient(circle at 72% 20%, var(--ghost-white) 0%, transparent 38%),
      radial-gradient(circle at 10% 70%, var(--ghost-teal) 0%, transparent 30%),
      radial-gradient(circle at 50% 95%, var(--ghost-white) 0%, transparent 32%);
  }
  .card--front .ghost-pattern {
    background:
      radial-gradient(circle at 75% 25%, var(--ghost-teal) 0%, transparent 36%),
      radial-gradient(circle at 90% 70%, rgba(220, 220, 220, 0.5) 0%, transparent 30%),
      radial-gradient(circle at 30% 85%, rgba(200, 230, 228, 0.5) 0%, transparent 30%);
  }
  .brand { position: absolute; display: flex; align-items: center; }
  .brand__mark { background: var(--turquoise); flex: none; }
  .brand__name {
    font-family: "Tinos", "Times New Roman", serif;
    color: var(--metal-grey);
    font-weight: 400;
    white-space: nowrap;
  }
  .card--back .brand { left: 143px; top: 143px; gap: 16px; }
  .card--back .brand__mark { width: 119px; height: 120px; }
  .card--back .brand__name { font-size: 50px; }
  .card--front .brand { left: 52px; top: 129px; gap: 10px; }
  .card--front .brand__mark { width: 79px; height: 77px; }
  .card--front .brand__name { font-size: 30px; }
  .divider {
    position: absolute; left: 356px; top: 118px;
    width: 1px; height: 100px; background: #777;
  }
  .holder {
    position: absolute; left: 370px; top: 150px;
    font-family: "Tinos", "Times New Roman", serif;
    color: var(--ink); text-align: center;
  }
  .holder__name { font-size: 28px; line-height: 32px; }
  .holder__role { font-size: 20px; line-height: 24px; }
  .contact {
    position: absolute; left: 38px; right: 40px; top: 311px;
    height: 64px;
    border-top: 1px solid var(--rule);
    border-bottom: 1px solid var(--rule);
    display: flex; justify-content: space-between;
    padding-top: 9px;
    font-size: 18px; line-height: 24px; color: #111;
  }
  .contact__label { display: inline-block; width: 58px; }
</style>
</head>
<body>
  <section class="card card--back">
    <div class="ghost-pattern" role="img" aria-label="Faint oversized curved ring pattern in white and pale turquoise"></div>
    <div class="brand">
      <span class="brand__mark"></span>
      <span class="brand__name">Velmont Estates</span>
    </div>
  </section>

  <section class="card card--front">
    <div class="ghost-pattern" role="img" aria-label="Faint oversized curved ring pattern in grey and pale turquoise"></div>
    <div class="brand">
      <span class="brand__mark"></span>
      <span class="brand__name">Velmont Estates</span>
    </div>
    <span class="divider"></span>
    <div class="holder">
      <p class="holder__name">Tobias Hennlund</p>
      <p class="holder__role">Managing Director</p>
    </div>
    <div class="contact">
      <div class="contact__direct">
        <p><span class="contact__label">Tel</span>: 083-274-6159</p>
        <p><span class="contact__label">email</span>: tobias@velmontestates.asia</p>
      </div>
      <div class="contact__web">
        <p>www.velmontestates.asia</p>
        <p>www.velmontestates.co.uk</p>
      </div>
    </div>
  </section>
</body>
</html>
```